Torvane Email Signature Banners – Fabrication Capability Series

www.Torvane.com.au is an Australian engineering and fabrication company specialising in fabrication and welding of :
steel piping spools,
skids and frames,
small volume process steel tanks
and general steel fabrication
We require four distinct banner designs for use in Microsoft Lintaro email signatures. Each banner will highlight a specific capability while maintaining a consistent brand identity.
Deliverables
Four banners total:
Piping Spools Fabrication – focus on precision welding and stainless steel pipework
Skid & Frames Fabrication – highlight skid systems and structural frames
Small Steel Tanks Fabrication – show fabricated tanks and workshop craftsmanship
General Fabrication Solutions – broad steel fabrication theme for company-wide use
Dimensions: 600–700 px wide × 100 px high
Format: PNG (preferred), small file size prefered
Resolution: 72 dpi
Background: non-transparent, industrial or workshop setting
Text examples:
1. Piping Spools Fabrication
Option A: “Expert Fabrication Solutions for Process Piping”
Option B: “Precision Welding for Complex Systems”
Option C: “Delivering Quality in Every Spool”
Option D: “Engineered for Flow, Built for Strength”
2. Skid & Frames Fabrication
Option A: “Custom Engineered Modular Systems”
Option B: “Built Strong. Designed Smart.”
Option C: “Reliable Frames for Industrial Performance”
Option D: “Modular Fabrication for Seamless Integration”
3. Small Steel Tanks Fabrication
Option A: “Precision Built for Your Needs”
Option B: “Compact Strength. Proven Durability.”
Option C: “Fabricated for Performance and Longevity”
Option D: “Small Tanks. Big Reliability.”
4. General Fabrication Solutions
Option A: “Quality Craftsmanship, Proven Results”
Option B: “Your Partner in Precision Fabrication”
Option C: “Engineering Excellence in Every Weld”
Option D: “Australian Fabrication. Global Standards.”
Style Direction
Clean, professional, and engineering‑focused
Use Torvane brand colours
Blend photo realism with vector clarity (no heavy gradients)
Include subtle industrial textures or workshop imagery
Typography: bold sans‑serif, legible at small scale
Usage Context
These banners will appear at the bottom of staff email signatures via Lintaro Email Signature Tool for Microsoft 365, so clarity and fast loading are essential. No Logo is required in the banners.
Reference
Existing Torvane signature is attached. Colour palette to match the signature style and logo.
Target Market(s)
Engineering and construction companies,
Industry/Entity Type
Engineering fabrication design
Look and feel

```html
<!DOCTYPE html>
<html lang="en">
<head>
<meta charset="UTF-8">
<title>Torvane Signature Banners</title>
<link rel="stylesheet" href="https://fonts.googleapis.com/css2?family=Rubik:wght@500;600&family=Exo+2:wght@400;500&display=swap">
<style>
  :root {
    --page: #ffffff;
    --panel: #1c2739;
    --panel-deep: #131b29;
    --accent: #2a8fd8;
    --accent-light: #3ba3ea;
    --text: #ffffff;
    --text-soft: #e4ebf3;
  }
  * { margin: 0; padding: 0; box-sizing: border-box; }
  html, body {
    width: 1200px; height: 482px; overflow: hidden;
    background: var(--page);
  }
  .sheet { position: relative; width: 1200px; height: 482px; }
  .banner {
    position: absolute; left: 85px; width: 1025px; height: 146px;
    overflow: hidden;
    background:
      radial-gradient(ellipse at 78% 35%, #23324b 0%, transparent 70%),
      linear-gradient(135deg, var(--panel) 0%, var(--panel-deep) 100%);
    box-shadow: 0 8px 14px rgba(0,0,0,0.28);
  }
  .banner--spools { top: 70px; }
  .banner--general { top: 264px; }
  .banner__stripe, .banner__photo {
    position: absolute; top: 0; left: 0; height: 100%;
  }
  .banner__stripe { background: linear-gradient(180deg, var(--accent-light), var(--accent)); }

  .banner--spools .banner__stripe { width: 568px; clip-path: polygon(0 0, 100% 0, 538px 100%, 0 100%); }
  .banner--spools .banner__photo {
    width: 556px; clip-path: polygon(0 0, 100% 0, 528px 100%, 0 100%);
    background: linear-gradient(90deg,
      #3e4652 0%, #7f8894 14%, #4a535f 28%, #9aa3ad 40%,
      #505b6a 54%, #7d93b4 68%, #a9bedc 78%, #62728a 90%, #3b4657 100%);
  }

  .banner--general .banner__stripe { width: 549px; clip-path: polygon(0 0, 100% 0, 519px 100%, 0 100%); }
  .banner--general .banner__photo {
    width: 537px; clip-path: polygon(0 0, 100% 0, 509px 100%, 0 100%);
    background: linear-gradient(90deg,
      #1f2631 0%, #4a4236 16%, #6a5a44 26%, #4d4a47 38%,
      #8d7a62 46%, #5b6673 60%, #3a4451 78%, #2a323e 100%);
  }

  .banner__copy { position: absolute; top: 0; height: 100%; color: var(--text); }
  .banner--spools .banner__copy { left: 576px; width: 430px; }
  .banner--general .banner__copy { left: 560px; width: 455px; }
  .banner__title {
    font-family: "Rubik", sans-serif; font-weight: 500;
    white-space: nowrap; line-height: 1;
  }
  .banner--spools .banner__title { font-size: 33px; margin-top: 19px; }
  .banner--general .banner__title { font-size: 32px; margin-top: 19px; }
  .banner__rule { height: 2px; background: var(--accent-light); margin: 14px 0 11px; }
  .banner--spools .banner__rule { width: 421px; }
  .banner--general .banner__rule { width: 420px; }
  .banner__tagline {
    font-family: "Exo 2", sans-serif; font-weight: 400;
    font-size: 19px; line-height: 1.3; color: var(--text-soft);
  }
</style>
</head>
<body>
<main class="sheet">
  <section class="banner banner--spools">
    <div class="banner__stripe"></div>
    <div class="banner__photo" role="img" aria-label="Welder joining stainless steel pipe spools and flanges with a bright arc in a workshop"></div>
    <div class="banner__copy">
      <h2 class="banner__title">Piping Spools Fabrication</h2>
      <div class="banner__rule"></div>
      <p class="banner__tagline">Expert Fabrication Solutions for<br>Process Piping</p>
    </div>
  </section>

  <section class="banner banner--general">
    <div class="banner__stripe"></div>
    <div class="banner__photo" role="img" aria-label="Gloved welder working on a steel pipe with sparks flying in a fabrication workshop"></div>
    <div class="banner__copy">
      <h2 class="banner__title">General Fabrication Solutions</h2>
      <div class="banner__rule"></div>
      <p class="banner__tagline">Your Partner in Precision<br>Fabrication</p>
    </div>
  </section>
</main>
</body>
</html>
```